Mosquito and outdoor pest management

The uploaded logo must be integrated as the main theme of the card. I would like it to be modern and eye catching. Maybe some backround images or light silver metallic background.
Space enough at the base for contact info to be put in- phone numbers,emails,names,website.
Space on the back for short blog and lines for hand writing..calling card.
Commercial- golf courses, schools, outdoor function properties, pre event treatments.
Residential- retirement villages, townhome complexes and general houses
Management

```html
<!DOCTYPE html>
<html lang="en">
<head>
<meta charset="utf-8">
<title>Harbour Mosquito – Business Card</title>
<link href="https://fonts.googleapis.com/css2?family=Crimson+Text:wght@600&family=Noto+Sans:wght@400;600&display=swap" rel="stylesheet">
<style>
  :root {
    --bg: #d9d6d1;
    --card: #f1f1f1;
    --ink: #111111;
    --red: #e0202b;
    --white: #ffffff;
  }
  * { margin: 0; padding: 0; box-sizing: border-box; }
  html, body { width: 1200px; height: 909px; overflow: hidden; background: var(--bg); }
  .canvas { position: relative; width: 1200px; height: 909px; }

  .card {
    position: absolute;
    width: 540px;
    height: 309px;
    background: var(--card);
    box-shadow: 0 6px 18px rgba(0,0,0,0.25);
    overflow: hidden;
  }
  .card-back { left: 60px; top: 120px; }
  .card-front { left: 600px; top: 480px; }

  /* back side */
  .service-group { position: absolute; left: 70px; }
  .service-group.commercial { top: 30px; }
  .service-group.residential { top: 180px; }
  .service-heading {
    font-family: "Crimson Text", serif;
    font-weight: 600;
    font-size: 28px;
    color: var(--red);
    line-height: 1;
    padding-bottom: 5px;
    border-bottom: 1.5px solid var(--red);
    width: 300px;
  }
  .service-list {
    list-style: none;
    margin: 10px 0 0 12px;
    font-family: "Noto Sans", sans-serif;
    font-size: 17px;
    color: var(--ink);
    line-height: 1.25;
  }

  /* front side */
  .wave { position: absolute; inset: 0; width: 540px; height: 309px; }
  .brand {
    position: absolute;
    left: 40px;
    top: 44px;
    display: flex;
    align-items: center;
    gap: 12px;
  }
  .brand-mark {
    width: 16px;
    height: 16px;
    border-radius: 50%;
    background: var(--red);
    flex: none;
  }
  .brand-name {
    font-family: "Noto Sans", sans-serif;
    font-weight: 600;
    font-size: 30px;
    line-height: 1;
    color: var(--ink);
  }

  .contact {
    position: absolute;
    right: 32px;
    top: 186px;
    text-align: right;
  }
  .contact-name {
    font-family: "Crimson Text", serif;
    font-weight: 600;
    font-size: 30px;
    color: var(--red);
    line-height: 1;
    margin-bottom: 10px;
  }
  .contact-line {
    display: flex;
    justify-content: flex-end;
    align-items: center;
    gap: 14px;
    font-family: "Noto Sans", sans-serif;
    font-size: 16px;
    color: var(--white);
    line-height: 1.5;
  }
  .contact-line svg { width: 13px; height: 13px; flex: none; }
</style>
</head>
<body>
<main class="canvas">

  <section class="card card-back" aria-label="Card back – services">
    <div class="service-group commercial">
      <h2 class="service-heading">Commercial</h2>
      <ul class="service-list">
        <li>schools</li>
        <li>golf courses</li>
        <li>pre event treatments</li>
        <li>outdoor function properties</li>
      </ul>
    </div>
    <div class="service-group residential">
      <h2 class="service-heading">Residential</h2>
      <ul class="service-list">
        <li>retirement villages</li>
        <li>townhome complexes and general houses</li>
      </ul>
    </div>
  </section>

  <section class="card card-front" aria-label="Card front – contact">
    <svg class="wave" viewBox="0 0 540 309" preserveAspectRatio="none" aria-hidden="true">
      <path d="M0,120 C20,200 90,225 170,212 C90,222 30,190 0,120 Z" fill="var(--red)"/>
      <path d="M0,130 C40,215 140,240 250,205 C350,172 420,110 540,150 L540,309 L0,309 Z" fill="var(--ink)"/>
      <path d="M330,135 C410,95 480,105 540,140 L540,150 C480,118 410,112 330,135 Z" fill="var(--red)"/>
    </svg>

    <div class="brand">
      <span class="brand-mark" aria-hidden="true"></span>
      <span class="brand-name">Harbour Mosquito</span>
    </div>

    <div class="contact">
      <div class="contact-name">Daniel Reeve</div>
      <div class="contact-line">061 2384 5590
        <svg viewBox="0 0 13 13"><rect width="13" height="13" rx="2" fill="var(--red)"/><path d="M3.5,3 l2,0 l0.6,2 l-1,0.8 a5,5 0 0 0 2.2,2.2 l0.8,-1 l2,0.6 l0,2 c-4,0 -6.6,-2.6 -6.6,-6.6 z" fill="var(--ink)"/></svg>
      </div>
      <div class="contact-line">www.harbourmosquito.com
        <svg viewBox="0 0 13 13"><rect width="13" height="13" rx="2" fill="var(--red)"/><circle cx="6.5" cy="6.5" r="3.6" fill="none" stroke="var(--ink)" stroke-width="1.2"/><line x1="2.9" y1="6.5" x2="10.1" y2="6.5" stroke="var(--ink)" stroke-width="1"/></svg>
      </div>
      <div class="contact-line">harbourmosquito@email.com
        <svg viewBox="0 0 13 13"><rect width="13" height="13" rx="2" fill="var(--red)"/><rect x="2.5" y="3.8" width="8" height="5.6" fill="none" stroke="var(--ink)" stroke-width="1.1"/><path d="M2.5,3.8 L6.5,7 L10.5,3.8" fill="none" stroke="var(--ink)" stroke-width="1.1"/></svg>
      </div>
    </div>
  </section>

</main>
</body>
</html>
```